Local business providing residential house cleaning services

We need a business card design that is "cute" or "cartoonish" while still maintaining a professional appeal. Tidal Sweepers is the name. We would like to use a "pin up girl" or maid next to the name with a broom or vacuum cleaner. We want the look to have a 50's American look to it. We are not sure if we want the pin up girl in a maid outfit or with a broom or vacuum cleaner but we hope some of you will be able to take these ideas and be creative. If you have any questions at all please don't hesitate to message me so that we can get the best design possible. Thank you very much and I look forward to seeing some designs! Mira Hollister

Target Market(s)

Upper class Americans that are busy and have money and want to come home to a clean house.

Industry/Entity Type

Cleaning Service

Contact Information for Business Card

Pin up girl incorporated into the card is a must.

Font styles to use
Decorative
Script

Requirements
Must have
• Pin up girl
Nice to have
• A crown used on the Q possibly.

```html
<!DOCTYPE html>
<html lang="en">
<head>
<meta charset="utf-8">
<title>Tidal Sweepers — Business Card</title>
<link rel="stylesheet" href="https://fonts.googleapis.com/css2?family=Source+Sans+3:wght@400;600&display=swap">
<style>
  :root {
    --backdrop-top: #2a2a2a;
    --backdrop-bottom: #050505;
    --card-front: #f3f3f3;
    --card-back: #c405d6;
    --brand-purple: #c100d3;
    --brand-brown: #3a1f14;
    --text-grey: #555555;
    --figure-tint: rgba(150, 0, 165, 0.45);
    --figure-brown: #4a2a1c;
  }
  * { box-sizing: border-box; margin: 0; padding: 0; }
  html, body { width: 1200px; height: 900px; overflow: hidden; }
  body {
    background: linear-gradient(180deg, var(--backdrop-top) 0%, #1a1a1a 45%, var(--backdrop-bottom) 100%);
    font-family: "Source Sans 3", "Myriad Pro", Arial, sans-serif;
    position: relative;
  }
  .card {
    position: absolute;
    top: 184px;
    width: 302px;
    height: 490px;
    border-radius: 12px;
    box-shadow: 0 6px 18px rgba(0,0,0,0.55);
    overflow: hidden;
  }
  .card--front { left: 299px; background: var(--card-front); }
  .card--back { left: 646px; width: 304px; background: var(--card-back); }

  .brand {
    position: absolute;
    left: 38px;
    top: 128px;
    display: flex;
    align-items: flex-end;
    gap: 10px;
  }
  .brand__figure {
    width: 46px;
    height: 78px;
    border-radius: 6px;
    background: var(--figure-brown);
    flex: none;
  }
  .brand__name {
    font-weight: 400;
    font-size: 41px;
    line-height: 0.98;
    color: var(--brand-brown);
    letter-spacing: 0.5px;
  }

  .contact {
    position: absolute;
    left: 0;
    right: 0;
    top: 258px;
    text-align: center;
    color: var(--text-grey);
    font-size: 13.5px;
    line-height: 17px;
  }
  .contact__name {
    color: var(--brand-purple);
    font-weight: 600;
    font-size: 17px;
    line-height: 20px;
  }
  .contact__block { margin-top: 12px; }
  .contact__block:first-of-type { margin-top: 0; }

  .back__figure {
    position: absolute;
    left: 58px;
    top: 56px;
    width: 200px;
    height: 400px;
    border-radius: 60px 60px 20px 20px;
    background: var(--figure-tint);
  }
  .back__name {
    position: absolute;
    left: 0;
    right: 0;
    top: 205px;
    text-align: center;
    color: #ffffff;
    font-weight: 400;
    font-size: 40px;
    line-height: 1.05;
  }
</style>
</head>
<body>
  <section class="card card--front" aria-label="Business card front">
    <div class="brand">
      <div class="brand__figure" role="img" aria-label="Silhouette of a pin-up woman holding a broom"></div>
      <div class="brand__name">Tidal<br>Sweepers</div>
    </div>
    <div class="contact">
      <div class="contact__block">
        <p class="contact__name">Dorian Pell</p>
        <p>Managing Director</p>
      </div>
      <div class="contact__block">
        <p>48 Harbor Lane</p>
        <p>Bayview, 204817.</p>
      </div>
      <div class="contact__block">
        <p>044-555 210 384</p>
        <p>hello@tidalsweepers.example</p>
        <p>www.tidalsweepers.example</p>
      </div>
    </div>
  </section>

  <section class="card card--back" aria-label="Business card back">
    <div class="back__figure" role="img" aria-label="Faint silhouette of a pin-up woman sweeping with a broom"></div>
    <p class="back__name">Tidal<br>Sweepers</p>
  </section>
</body>
</html>
```